Lumaris Project 1 - Business Card For Co-Owners

We are an all women's gym located in Seattle, WA. We have been working the past year to elevate our brand and are looking for high quality business card design. I'm including some variations of our logo and have also included an inspiration photo. Our new website is launching on Feb 1 to give you a better idea about who we are (lumaristudio.example). We really love the inspiration business card, some of the key points we like about it:
- the geometric pattern on the back side with gloss texture.
- the rounded corners.
- the simple, clean, strong, yet feminine aesthetic.

Target Market(s)

Women - ages 18-65

Contact Information for Business Card

Company Logo
Company Name
Name
Title
Phone
Email
Website

Font styles to use
Other font styles liked:
• Futura (SEE NOTES)

Colors
e34297

Requirements
Must have
• We really love the inspiration business card, some of the key points we like about it:
• - the geometric pattern on the back side with gloss texture.
• - the dark front side with info.
• - the rounded corners.
• - the simple, clean, strong, yet feminine aesthetic.
• See Logo attached for colors - can be a slight variation of the pink of works better on a dark background
Nice to have
• Futura is one of the fonts used in our logo, but any font that complements the logo will work. I played around a little with design and wasn't wowed by the look of futura, but I'm also not a designer :)
• - the rounded corners.

```html
<!DOCTYPE html>
<html lang="en">
<head>
<meta charset="UTF-8">
<title>Lumaris Business Card</title>
<link rel="stylesheet" href="https://fonts.googleapis.com/css2?family=Montserrat:wght@500;600;800&display=swap">
<style>
  :root {
    --pink: #e0359a;
    --pink-deep: #c81f86;
    --pink-light: #ef5fb3;
    --pink-sheen: rgba(255,255,255,0.16);
    --ink: #1d1d1f;
    --ink-soft: #2c2c2e;
    --white: #ffffff;
    --canvas: #ececec;
  }
  * { margin: 0; padding: 0; box-sizing: border-box; }
  html, body { width: 1200px; height: 1000px; overflow: hidden; }
  body {
    background: var(--canvas);
    font-family: "Montserrat", sans-serif;
    position: relative;
  }
  .card {
    position: absolute;
    left: 300px;
    width: 600px;
    height: 343px;
    border-radius: 22px;
    overflow: hidden;
    box-shadow: 0 10px 28px rgba(0,0,0,0.18);
  }

  /* Back side */
  .card-back { top: 110px; }
  .back-pattern {
    position: absolute; inset: 0;
    background:
      linear-gradient(135deg, var(--pink-sheen) 0%, transparent 45%, var(--pink-sheen) 70%, transparent 100%),
      radial-gradient(ellipse at 40% 30%, var(--pink-light), var(--pink) 55%, var(--pink-deep));
  }
  .back-brand {
    position: absolute; left: 0; right: 0; top: 118px;
    text-align: center; color: var(--white);
  }
  .brand-name {
    font-weight: 800;
    font-size: 64px;
    letter-spacing: 3px;
    line-height: 1;
  }
  .brand-tagline {
    font-weight: 500;
    font-size: 22px;
    letter-spacing: 4px;
    margin-top: 8px;
  }

  /* Front side */
  .card-front {
    top: 530px;
    background: linear-gradient(160deg, var(--ink-soft), var(--ink) 60%, #151516);
  }
  .front-frame {
    position: absolute; inset: 12px;
    border: 3px solid var(--pink);
    border-radius: 14px;
  }
  .front-brand {
    position: absolute; left: 38px; top: 92px; color: var(--white);
  }
  .front-brand .brand-name { font-size: 52px; }
  .front-brand .brand-tagline { font-size: 18px; margin-top: 6px; }
  .person {
    position: absolute; right: 38px; top: 36px; text-align: right;
  }
  .person-name {
    font-weight: 600; font-size: 26px; letter-spacing: 2px; color: var(--white); line-height: 1.1;
  }
  .person-name .surname { color: var(--pink); }
  .person-title {
    font-weight: 600; font-size: 15px; letter-spacing: 4px; color: var(--white); margin-top: 2px;
  }
  .address {
    position: absolute; right: 38px; top: 160px;
    display: flex; align-items: flex-start; gap: 12px;
    color: var(--white); font-weight: 500; font-size: 16px; line-height: 1.45;
  }
  .contacts {
    position: absolute; left: 38px; bottom: 34px;
    list-style: none; color: var(--white); font-weight: 500; font-size: 17px;
  }
  .contacts li { display: flex; align-items: center; gap: 12px; margin-top: 8px; }
  .icon {
    width: 28px; height: 28px; border-radius: 7px;
    background: var(--pink);
    display: flex; align-items: center; justify-content: center;
    flex-shrink: 0;
  }
  .icon svg { width: 18px; height: 18px; }
</style>
</head>
<body>

  <section class="card card-back" aria-label="Card back">
    <div class="back-pattern" role="img" aria-label="Glossy pink geometric pattern of repeating rounded squares covers the back"></div>
    <div class="back-brand">
      <div class="brand-name">LUMARIS</div>
      <div class="brand-tagline">RISE AND SHINE</div>
    </div>
  </section>

  <section class="card card-front" aria-label="Card front">
    <div class="front-frame"></div>

    <div class="person">
      <div class="person-name">JANE<span class="surname">ROWE</span></div>
      <div class="person-title">OWNER</div>
    </div>

    <div class="front-brand">
      <div class="brand-name">LUMARIS</div>
      <div class="brand-tagline">RISE AND SHINE</div>
    </div>

    <div class="address">
      <span class="icon">
        <svg viewBox="0 0 24 24" fill="none" stroke="#fff" stroke-width="2.2">
          <path d="M12 21s-6-6.2-6-11a6 6 0 0 1 12 0c0 4.8-6 11-6 11z"/>
          <circle cx="12" cy="10" r="2.2"/>
        </svg>
      </span>
      <div>1200 Harbor Ave SW<br>Seattle, WA 98126</div>
    </div>

    <ul class="contacts">
      <li>
        <span class="icon">
          <svg viewBox="0 0 24 24" fill="none" stroke="#fff" stroke-width="2.2">
            <rect x="7" y="3" width="10" height="18" rx="2"/>
            <line x1="11" y1="18" x2="13" y2="18"/>
          </svg>
        </span>206.555.0148
      </li>
      <li>
        <span class="icon">
          <svg viewBox="0 0 24 24" fill="none" stroke="#fff" stroke-width="2.2">
            <rect x="3" y="6" width="18" height="12" rx="1.5"/>
            <path d="M3 7l9 6 9-6"/>
          </svg>
        </span>hello@lumaristudio.example
      </li>
      <li>
        <span class="icon">
          <svg viewBox="0 0 24 24" fill="none" stroke="#fff" stroke-width="2">
            <circle cx="12" cy="12" r="8.5"/>
            <ellipse cx="12" cy="12" rx="3.8" ry="8.5"/>
            <line x1="3.5" y1="12" x2="20.5" y2="12"/>
          </svg>
        </span>lumaristudio.example
      </li>
    </ul>
  </section>

</body>
</html>
```